KVR Inc Web Design

WHAT ARE WE DOING?
We are developing a new website look and feel for a new company called KVR Inc. This new look and feel should include colors, design elements, choice of photography and other imagery, fonts, and other user experience elements.

WHAT DO THEY DO?
KVR, Inc, makes tools for researchers who are studying protein-protein interactions. These molecules are the basic tools of biology, and serve as key targets for drug developers and disease researchers. The world of proteins is enormously complex, and companies like KVR provide researchers with critical tools that help them elucidate this world.

WHO ARE WE TALKING TO?
The target audience for this website are professional scientists working in university research or biopharma drug development. They are highly sophisticated consumers looking for key tools that will advance their research.

WHAT DO WE WANT THEM TO DO?
The site is an information resource for the customer exploring the tools that KVR sells and the scientific issues surrounding protein-protein interactions. They should be able to navigate easily to their content of choice, while the whole site should convey a professionalism that enhanced KVR’s credibility.

WHAT DOES THE KVR BRAND STAND FOR?
KVR stands for illumination. Proteins are challenging to study, and KVR exists to help shed light on their workings.

WHAT ARE THE KEY VALUES OF THE KVR BRAND?
Integrity. Innovation. Insight.

WHAT ARE THE EXECUTIONAL MANDITORIES?
The look and feel is completely up for grabs. Nothing is off the table.

WHAT ARE THE DELIVERABLES?
We need new designs for the following templates:
http://cms.marlowbench.com/
http://cms.marlowbench.com/products-and-services/instruments-3/bench-top-instruments/
http://cms.marlowbench.com/category/lab-study/

```html
<!DOCTYPE html>
<html lang="en">
<head>
<meta charset="utf-8">
<title>Pipettes – KVR Inc</title>
<link rel="stylesheet" href="https://fonts.googleapis.com/css2?family=Mulish:ital,wght@0,400;0,600;0,700;1,400&family=Open+Sans:wght@400&display=swap">
<style>
  :root {
    --orange: #f9ae3b;
    --blue: #33b3d7;
    --text: #5f5f5f;
    --dark: #222;
    --muted: #a2a2a2;
    --line: #d9d9d9;
    --tab: #e3e3e3;
    --footer: #6c6c6c;
    --page: #fff;
  }
  * { box-sizing: border-box; margin: 0; padding: 0; }
  html, body { width: 1195px; height: 1200px; overflow: hidden; background: var(--page); }
  body { font-family: "Mulish", Arial, sans-serif; color: var(--text); position: relative; }
  a { color: inherit; text-decoration: none; }

  .site-header { position: absolute; top: 0; left: 0; width: 1195px; height: 61px; border-top: 3px solid var(--orange); border-bottom: 1px solid #e6e6e6; box-shadow: 0 1px 3px rgba(0,0,0,.05); }
  .brand { position: absolute; left: 120px; top: 13px; font-size: 29px; font-weight: 400; letter-spacing: 6px; color: #6a6a6a; line-height: 30px; }
  .main-nav { position: absolute; top: 19px; left: 0; display: flex; font-size: 16px; font-weight: 700; color: #6a6a6a; }
  .main-nav a { position: absolute; white-space: nowrap; }
  .main-nav .active { color: var(--orange); }
  .search { position: absolute; left: 938px; top: 16px; width: 138px; height: 25px; background: linear-gradient(#8e8e8e, #7d7d7d); border-radius: 2px; color: #e8e8e8; font-size: 13px; padding: 5px 8px; }
  .search svg { position: absolute; right: 7px; top: 6px; }

  .sidebar { position: absolute; left: 120px; top: 88px; width: 219px; height: 506px; box-shadow: 0 1px 3px rgba(0,0,0,.3); background: #fff; }
  .panel-title { background: var(--blue); color: #fff; font-weight: 700; font-size: 18px; height: 40px; line-height: 40px; padding-left: 18px; }
  .product-list { list-style: none; padding: 8px 0 18px; }
  .product-list li { height: 33px; line-height: 33px; padding-left: 32px; font-size: 15.5px; color: var(--dark); position: relative; }
  .product-list li::before { content: "»"; position: absolute; left: 19px; top: -1px; font-size: 13px; }
  .product-list li.current { background: var(--orange); color: #fff; }
  .news-item { padding: 18px 18px 12px; border-bottom: 1px solid #e6e6e6; font-size: 13px; line-height: 17px; color: #555; }
  .news-item:last-child { border-bottom: 0; }
  .news-date { font-style: italic; color: var(--muted); margin-bottom: 1px; }

  .content { position: absolute; left: 365px; top: 88px; width: 711px; }
  .page-title { font-size: 27px; font-weight: 400; color: var(--dark); height: 33px; line-height: 27px; border-bottom: 4px double #aaa; }
  .lead { font-size: 20.5px; line-height: 24px; color: var(--dark); margin-top: 17px; }
  .photo-frame { border: 1px solid var(--line); padding: 6px; margin-top: 17px; }
  .photo { height: 285px; background: linear-gradient(100deg, #ccd6dc 0%, #e7ecee 35%, #f4f4f2 60%, #dfd6cc 100%); }
  .body-copy { margin-top: 20px; font-size: 13.2px; line-height: 18.7px; }
  .body-copy p + p { margin-top: 18.7px; }
  .hl { color: var(--orange); font-weight: 600; }

  .tabs { margin-top: 35px; border: 1px solid var(--line); }
  .tab-bar { display: flex; height: 35px; font-family: "Open Sans", Arial, sans-serif; font-size: 15.5px; }
  .tab { background: var(--tab); color: #666; text-align: center; line-height: 35px; border-left: 1px solid #fff; position: relative; }
  .tab:first-child { border-left: 0; }
  .tab.selected { background: var(--blue); color: #fff; }
  .tab.selected::after { content: ""; position: absolute; left: 50%; bottom: -6px; margin-left: -6px; border: 6px solid transparent; border-bottom: 0; border-top-color: var(--blue); }
  .tab-panel { display: flex; padding: 25px 19px 17px 23px; height: 307px; }
  .tab-photo-frame { border: 1px solid var(--line); padding: 6px; width: 255px; height: 255px; flex: none; }
  .tab-photo { width: 100%; height: 100%; background: linear-gradient(135deg, #2e5fa8 0%, #4d80c4 45%, #b9aa8e 75%, #2b4f86 100%); }
  .tab-copy { margin-left: 13px; font-size: 13.2px; line-height: 18.7px; margin-top: 3px; }
  .tab-copy p + p { margin-top: 18.7px; }

  .site-footer { position: absolute; left: 0; top: 1138px; width: 1195px; height: 62px; background: var(--footer); color: #fff; font-size: 13px; }
  .footer-nav { position: absolute; left: 120px; top: 25px; }
  .footer-nav span { margin: 0 6px; }
  .social { position: absolute; left: 821px; top: 20px; display: flex; gap: 6px; }
  .social span { width: 24px; height: 24px; border-radius: 50%; background: #fff; display: block; }
  .copyright { position: absolute; left: 925px; top: 25px; font-size: 14px; }
  .copyright b { color: var(--orange); font-weight: 400; }
</style>
</head>
<body>
  <header class="site-header">
    <div class="brand">KVR INC</div>
    <nav class="main-nav">
      <a style="left:303px">Company</a>
      <a class="active" style="left:396px">Products &amp; Services</a>
      <a style="left:559px">Learning Center</a>
      <a style="left:697px">Events</a>
      <a style="left:767px">KVR News</a>
      <a style="left:858px">Contact</a>
    </nav>
    <div class="search">Search
      <svg width="13" height="13" viewBox="0 0 13 13"><circle cx="5.5" cy="5.5" r="4.2" fill="none" stroke="#cfcfcf" stroke-width="1.5"/><path d="M8.5 8.5 12 12" stroke="#cfcfcf" stroke-width="1.8"/></svg>
    </div>
  </header>

  <aside class="sidebar">
    <div class="panel-title">Product Overview</div>
    <ul class="product-list">
      <li>Reagents</li>
      <li class="current">Pipettes</li>
      <li>Tubes</li>
    </ul>
    <div class="panel-title">Latest News</div>
    <div class="news-item">
      <div class="news-date">October 17, 2013</div>
      Lorem ipsum dolor sit &nbsp;amet, consect etureius mod dipisi cing elit, sed do eiusmod tempor mod &gt;&gt;&gt;
    </div>
    <div class="news-item">
      <div class="news-date">October 17, 2013</div>
      Lorem ipsum dolor sit &nbsp;amet, consect etureius mod dipisi cing elit, sed do eiusmod tempor mod &gt;&gt;&gt;
    </div>
  </aside>

  <main class="content">
    <h1 class="page-title">PIPETTES</h1>
    <p class="lead">Donec non massa lacinia, commodo eros eget, rutrum arcu. Integer unt ncid unt, velit id eleifend congue, odio massa consequat mauris,</p>
    <div class="photo-frame">
      <div class="photo" role="img" aria-label="Researchers in a laboratory examining a flask of blue liquid beside coloured glassware"></div>
    </div>
    <div class="body-copy">
      <p>Quisque feugiat lacus vitae posuere blandit. Nulla sit amet laoreet felis, id rhoncus nisl. Aenean fringilla quam in nibh egestas, in malesuada tortor accumsan. Donec non massa lacinia, commodo eros eget, rutrum arcu. Integer tincidunt, velit id eleifend congue, odio massa consequat mauris, a scelerisque nulla nulla eu nulla. Cras luctus pulvinar nibh ut viverra. Aenean vestibulum vitae justo non dictum. Mauris ut tellus in dui pretium dictum nec non tortor. Nulla a velit quis dolor interdum scelerisque eu et nisl.</p>
      <p>Donec auctor mollis ligula eget molestie. Aliquam erat volutpat. Curabitur sapien libero, condimentum ac nisl ultricies tincidunt ipsum. Donec in iaculis metus. Mauris eleifend nisi non sapien commodo, hendrerit consectetur. Pellentesque faucibus, purus non dictum lacinia, ante augue pretium neque, vitae egestas dui nisi et enim. ornare Suspendisse nibh vel lacinia rhoncus Donec auctor mollis ligula eget molestie. Pellentesque faucibus, purus non dictum lacinia, ante augue pretium neque, <span class="hl">vitae egestas</span> dui nisi et enim. Suspendisse iaculis nibh vel lacinia rhoncus</p>
    </div>

    <section class="tabs">
      <div class="tab-bar">
        <div class="tab selected" style="width:140px">Overview</div>
        <div class="tab" style="width:142px">Features</div>
        <div class="tab" style="width:168px">Specifications</div>
        <div class="tab" style="width:125px">FAQ's</div>
        <div class="tab" style="width:134px">Manuals</div>
      </div>
      <div class="tab-panel">
        <div class="tab-photo-frame">
          <div class="tab-photo" role="img" aria-label="Gloved hands using a pipette over a test tube in blue lab light"></div>
        </div>
        <div class="tab-copy">
          <p>Quisque feugiat lacus vitae posuere blandit. Nulla sit amet laoreet felis, id rhoncus nisl. Aenean fringilla quam in nibh egestas, in malesuada tortor accumsan. Donec non massa lacinia, commodo eros eget, rutrum arcu. Integer tincidunt, velit id eleifend congue, odio massa consequat mauris, a scelerisque nulla nulla eu nulla. Cras luctus pulvinar nibh ut viverra. Aenean vestibulum vitae justo non dictum. Mauris ut tellus in dui pretium dictum nec non tortor. Nulla a velit quis dolor interdum <span class="hl">scelerisque</span> eu et nisl.</p>
          <p>Donec auctor mollis ligula eget molestie. Aliquam erat volutpat. Curabitur sapien libero, condimentum ac nisl nec, ultricies tincidunt ipsum. Donec in iaculis metus. Mauris eleifend nisi non sapien commodo, hendrerit ornare lacus consectetur. Pellentesque faucibus, purus non dictum lacinia,</p>
        </div>
      </div>
    </section>
  </main>

  <footer class="site-footer">
    <nav class="footer-nav">Company<span>-</span>Products &amp; Services<span>-</span>Learning Center<span>-</span>Events<span>-</span>KVR News<span>-</span>Contact</nav>
    <div class="social" aria-label="Social links"><span></span><span></span><span></span></div>
    <div class="copyright">Copyright © <b>KVR Inc.</b> 2013</div>
  </footer>
</body>
</html>
```